"Vine Hollow Excursions" is a top notch Santa Barbara County Wine Tour company.

We provide scenic, boutique and custom wine tours. I need the card to be clean and classy. I will provide our logo. I would like the logo to cover the back side of the card as an option and would like to see a couple color options other then our signature green and gold. I would like to see some creative options and let the designers come up with options.
I need cards for myself and my team. The final design should communicate "An authentic and boutique wine tour experience"
Please use my website for reference www.vinehollowexcursions.example

Target Market(s)

We have a wide range of clients from millennials to baby boomers

Industry/Entity Type

Tour

Contact Information for Business Card

Contact info:
Dale Morton
805-219-6384
info@vinehollowexcursions.example
vinehollowexcursions.example

Colors

Designer to choose colors to be used in the design.

Requirements
Must have
• my logo
Nice to have
• *I would like to have the backside side with the logo and the company statement
• "An authentic and boutique wine tour experience" as an option.
• *I would also like to see what the designers can create!
• *I would like to see an option that incorporates or social: instagram, yelp, trip advisor
Should not have
• I do not want it too busy.

```html
<!DOCTYPE html>
<html lang="en">
<head>
<meta charset="utf-8">
<title>Vine Hollow Excursions – Business Card</title>
<link rel="stylesheet" href="https://fonts.googleapis.com/css2?family=Roboto:wght@400;500&family=Roboto+Condensed:wght@700&display=swap">
<style>
  :root {
    --backdrop: #2a2a2a;
    --paper: #f3f3f1;
    --green: #276743;
    --green-deep: #2a6a45;
    --gold-light: #c9b48f;
    --gold-dark: #7d6a52;
    --ink: #444444;
    --white: #ffffff;
    --haze: #dfe5df;
  }
  * { margin: 0; padding: 0; box-sizing: border-box; }
  html, body { width: 1200px; height: 960px; overflow: hidden; }
  body {
    position: relative;
    background: var(--backdrop);
    font-family: "Roboto", Arial, sans-serif;
  }
  .card {
    position: absolute;
    width: 600px;
    height: 343px;
    overflow: hidden;
    box-shadow: 0 3px 8px rgba(0,0,0,0.45);
  }
  /* Front */
  .card-front { left: 314px; top: 113px; background: var(--paper); }
  .sunrise-decoration {
    position: absolute;
    left: 250px; top: 10px;
    width: 350px; height: 310px;
    background: radial-gradient(ellipse at 70% 80%, var(--haze) 0%, rgba(223,229,223,0.45) 35%, rgba(243,243,241,0) 70%);
  }
  .brand-name {
    position: absolute;
    left: 36px; top: 112px;
    width: 240px;
    font-family: "Roboto", Arial, sans-serif;
    font-weight: 500;
    font-size: 21px;
    color: var(--gold-dark);
    white-space: nowrap;
  }
  .brand-region {
    position: absolute;
    left: 37px; top: 150px;
    font-size: 9px;
    letter-spacing: 2.6px;
    color: var(--green);
    text-transform: uppercase;
  }
  .rule-gold {
    position: absolute;
    left: 246px; top: 140px;
    width: 320px; height: 1px;
    background: var(--gold-dark);
  }
  .person-name {
    position: absolute;
    right: 34px; top: 110px;
    font-family: "Roboto Condensed", "Arial Narrow", sans-serif;
    font-weight: 700;
    font-size: 21px;
    color: var(--green-deep);
    text-transform: uppercase;
  }
  .contact-list {
    position: absolute;
    left: 38px; top: 247px;
    list-style: none;
    font-size: 14px;
    color: var(--ink);
    line-height: 20px;
  }
  .contact-list li { display: flex; align-items: center; gap: 6px; }
  .contact-list svg { width: 13px; height: 13px; fill: var(--green); flex: none; }
  .band-gold {
    position: absolute;
    left: 0; top: 318px;
    width: 350px; height: 10px;
    background: linear-gradient(90deg, var(--gold-dark), var(--gold-light) 60%, var(--gold-dark));
  }
  .band-green {
    position: absolute;
    left: 0; top: 328px;
    width: 600px; height: 15px;
    background: var(--green);
  }
  .web-tab {
    position: absolute;
    left: 336px; top: 296px;
    width: 264px; height: 47px;
    background: var(--green);
    clip-path: polygon(22px 0, 100% 0, 100% 100%, 0 100%);
    border-top: 2px solid var(--white);
  }
  .web-address {
    position: absolute;
    right: 26px; top: 312px;
    font-size: 13.5px;
    color: var(--white);
  }
  /* Back */
  .card-back { left: 311px; top: 472px; background: var(--green); }
  .social-links {
    position: absolute;
    right: 29px; top: 30px;
    display: flex; gap: 4px;
    list-style: none;
  }
  .social-links li {
    width: 32px; height: 32px;
    border-radius: 5px;
    border: 1px solid rgba(0,0,0,0.25);
  }
  .social-links .badge-a { background: #d8c3a0; }
  .social-links .badge-b { background: #5a9a3c; }
  .social-links .badge-c { background: #d9312c; }
  .back-brand {
    position: absolute;
    left: 0; top: 145px;
    width: 600px;
    text-align: center;
    font-weight: 500;
    font-size: 36px;
    color: var(--white);
  }
  .tagline {
    position: absolute;
    left: 0; top: 293px;
    width: 600px;
    text-align: center;
    font-size: 15px;
    color: var(--white);
  }
</style>
</head>
<body>
  <section class="card card-front">
    <div class="sunrise-decoration" role="img" aria-label="Faint sunrise over hills decoration"></div>
    <div class="brand-name">Vine Hollow Excursions</div>
    <div class="brand-region">Santa Barbara County</div>
    <div class="rule-gold"></div>
    <div class="person-name">Dale Morton</div>
    <ul class="contact-list">
      <li><svg viewBox="0 0 24 24" aria-hidden="true"><path d="M6.6 10.8a15.1 15.1 0 0 0 6.6 6.6l2.2-2.2a1 1 0 0 1 1-.25 11.4 11.4 0 0 0 3.6.57 1 1 0 0 1 1 1V20a1 1 0 0 1-1 1A17 17 0 0 1 3 4a1 1 0 0 1 1-1h3.5a1 1 0 0 1 1 1c0 1.25.2 2.45.57 3.57a1 1 0 0 1-.25 1z"/></svg>805-219-6384</li>
      <li><svg viewBox="0 0 24 24" aria-hidden="true"><path d="M2 5h20v14H2z M2 5l10 7 10-7" fill="none" stroke="#276743" stroke-width="0"/><path d="M2 6.5 12 13l10-6.5V19H2z"/><path d="M2 5h20L12 11.5z"/></svg>info@vinehollowexcursions.example</li>
    </ul>
    <div class="band-gold"></div>
    <div class="band-green"></div>
    <div class="web-tab"></div>
    <div class="web-address">www.vinehollowexcursions.example</div>
  </section>

  <section class="card card-back">
    <ul class="social-links">
      <li class="badge-a"></li>
      <li class="badge-b"></li>
      <li class="badge-c"></li>
    </ul>
    <div class="back-brand">Vine Hollow Excursions</div>
    <p class="tagline">An authentic &amp; boutique wine tour experience</p>
  </section>
</body>
</html>
```